Car transport business

We need a new business card design. Attached is our old card sample. I would just like to adjust the logo colors (blue and red) to be brighter. I changed my name to the brighter red and the word dispatcher to a brighter blue as an example. But you can adjust those colors further. And then perhaps you can use the same colors for the card design but use your imagination.

As a suggestion so the card stands out I would like to add a clip art of car carrier truck. Attached are examples of that as well

```html
<!DOCTYPE html>
<html lang="en">
<head>
<meta charset="UTF-8">
<title>Summit Haul – Business Card</title>
<link rel="stylesheet" href="https://fonts.googleapis.com/css2?family=Montserrat:wght@600;800&family=Mulish:wght@400;600&display=swap">
<style>
  :root {
    --bg: #d9d9db;
    --card-white: #ffffff;
    --brand-blue: #0b66c2;
    --brand-blue-deep: #0553a3;
    --brand-blue-bright: #1a6fd6;
    --brand-red: #e5121c;
    --tagline: #cfe3ff;
    --ink: #3a3a3a;
    --art-tone: #e9eaec;
    --art-tone-dark: #bfc1c5;
  }
  * { box-sizing: border-box; margin: 0; padding: 0; }
  html, body { width: 1200px; height: 800px; overflow: hidden; }
  body {
    background: var(--bg);
    font-family: "Mulish", sans-serif;
    position: relative;
  }
  .card {
    position: absolute;
    width: 540px;
    height: 310px;
    border-radius: 22px;
    overflow: hidden;
    box-shadow: 0 10px 24px rgba(0,0,0,0.18);
  }

  /* Contact side */
  .card--contact {
    left: 40px;
    top: 140px;
    background: var(--card-white);
  }
  .truck-art {
    position: absolute;
    right: 24px;
    top: 22px;
    width: 216px;
    height: 170px;
    border-radius: 10px;
    background: linear-gradient(135deg, var(--art-tone), var(--art-tone-dark));
  }
  .identity {
    position: absolute;
    left: 40px;
    bottom: 34px;
    width: 250px;
  }
  .person-name {
    font-family: "Montserrat", sans-serif;
    font-weight: 800;
    font-size: 30px;
    letter-spacing: 0.5px;
    line-height: 1;
    white-space: nowrap;
  }
  .person-name .first { color: var(--brand-blue-bright); }
  .person-name .last { color: var(--brand-red); }
  .person-role {
    font-size: 15px;
    color: var(--brand-red);
    margin: 4px 0 14px;
  }
  .contact-list { list-style: none; }
  .contact-list li {
    display: flex;
    align-items: center;
    gap: 10px;
    font-size: 14px;
    color: var(--ink);
    line-height: 1.55;
    white-space: nowrap;
  }
  .contact-list svg { width: 15px; height: 15px; flex: none; }

  /* Brand side */
  .card--brand {
    left: 620px;
    top: 350px;
    background: linear-gradient(160deg, var(--brand-blue-bright), var(--brand-blue-deep));
    display: flex;
    flex-direction: column;
    align-items: center;
    justify-content: center;
    text-align: center;
  }
  .brand-name {
    font-family: "Montserrat", sans-serif;
    font-weight: 800;
    font-size: 44px;
    letter-spacing: 3px;
    color: var(--card-white);
    line-height: 1;
  }
  .brand-tagline {
    font-family: "Montserrat", sans-serif;
    font-weight: 600;
    font-size: 12px;
    letter-spacing: 4px;
    color: var(--tagline);
    margin-top: 12px;
  }
  .brand-web {
    font-size: 15px;
    letter-spacing: 1px;
    color: var(--card-white);
    margin-top: 46px;
  }
  .brand-web strong { font-weight: 600; }
</style>
</head>
<body>

  <section class="card card--contact">
    <div class="truck-art" role="img" aria-label="Illustration of a car carrier truck"></div>

    <div class="identity">
      <h1 class="person-name"><span class="first">RENO</span> <span class="last">VALDE</span></h1>
      <p class="person-role">Dispatcher</p>
      <ul class="contact-list">
        <li>
          <svg viewBox="0 0 16 16" aria-hidden="true"><circle cx="8" cy="8" r="8" fill="#e5121c"/><path d="M5.2 4.2l1.5 1.5-.8 1c.5 1 1.3 1.8 2.3 2.3l1-.8 1.5 1.5-1 1c-2.7-.4-4.9-2.6-5.3-5.3z" fill="#fff"/></svg>
          555-201-0148
        </li>
        <li>
          <svg viewBox="0 0 16 16" aria-hidden="true"><circle cx="8" cy="8" r="8" fill="#e5121c"/><rect x="5.5" y="3.5" width="5" height="9" rx="1" fill="#fff"/></svg>
          555-201-0172
        </li>
        <li>
          <svg viewBox="0 0 16 16" aria-hidden="true"><circle cx="8" cy="8" r="8" fill="#e5121c"/><rect x="4" y="5" width="8" height="6" fill="#fff"/><path d="M4 5l4 3.2L12 5" stroke="#e5121c" stroke-width="1" fill="none"/></svg>
          summithaulco@mail.com
        </li>
        <li>
          <svg viewBox="0 0 16 16" aria-hidden="true"><circle cx="8" cy="8" r="8" fill="#e5121c"/><circle cx="8" cy="8" r="3.8" fill="none" stroke="#fff" stroke-width="1.2"/><path d="M4.2 8h7.6" stroke="#fff" stroke-width="1"/></svg>
          www.summithaulco.com
        </li>
      </ul>
    </div>
  </section>

  <section class="card card--brand">
    <h2 class="brand-name">SUMMIT HAUL</h2>
    <p class="brand-tagline">THE AUTO TRANSPORT PROFESSIONALS</p>
    <p class="brand-web">www.<strong>SummitHaulCo</strong>.com</p>
  </section>

</body>
</html>
```